Business Card Design (NEW FILES)

ATTENTION: New vector files are available. Please update your design to reflect/use the new (better resolution) logo images.

Seeking a unique and professional business card design for a commercial drone photography/videography business. The layout should feature
the logo (attached) and include the following information:
Owen Tarrick
614-502-7738
www.skylarkreelworks.example
NRD Certified Remote Pilot

Owen Tarrick

```html
<!DOCTYPE html>
<html lang="en">
<head>
<meta charset="utf-8">
<title>Skylark Reelworks – Business Card</title>
<link rel="stylesheet" href="https://fonts.googleapis.com/css2?family=Open+Sans:wght@400;600;700&display=swap">
<style>
  :root {
    --backdrop: #222222;
    --navy: #1a1c4c;
    --navy-deep: #15173f;
    --emboss: #27358a;
    --orange: #ec8a4c;
    --white: #ffffff;
  }
  * { margin: 0; padding: 0; box-sizing: border-box; }
  html, body {
    width: 1200px; height: 780px; overflow: hidden;
    background: var(--backdrop);
    font-family: "Open Sans", Arial, sans-serif;
  }
  .canvas {
    width: 1200px; height: 780px;
    display: flex; align-items: center; justify-content: center; gap: 44px;
  }
  .card {
    position: relative;
    width: 520px; height: 297px;
    background: var(--navy);
    box-shadow: 0 18px 40px rgba(0,0,0,.55);
    overflow: hidden;
  }
  /* Front: contact side */
  .brand {
    position: absolute; left: 36px; top: 62px;
    display: flex; align-items: center; gap: 10px;
  }
  .brand-dot {
    width: 22px; height: 22px; border-radius: 50%;
    background: var(--white);
  }
  .brand-name {
    color: var(--white); font-weight: 600; font-size: 21px;
    letter-spacing: .5px;
  }
  .credentials {
    position: absolute; left: 20px; width: 230px; top: 196px;
    text-align: center; color: var(--white);
    font-size: 14px; line-height: 22px;
  }
  .divider { position: absolute; left: 0; top: 0; }
  .person { position: absolute; left: 290px; top: 92px; }
  .person-name { font-size: 29px; font-weight: 700; line-height: 1.05; }
  .person-name .first { color: var(--orange); }
  .person-name .last { color: var(--white); }
  .person-role { color: var(--white); font-size: 13px; margin-top: 2px; }
  .contacts { list-style: none; margin-top: 14px; }
  .contacts li {
    display: flex; align-items: center; gap: 9px;
    color: var(--white); font-size: 13px; line-height: 22px;
  }
  .contacts svg { width: 13px; height: 13px; flex: none; }
  /* Back: embossed name */
  .card-back { background: var(--navy-deep); }
  .emboss-mark {
    position: absolute; inset: 0;
    display: flex; align-items: center; justify-content: center; gap: 14px;
  }
  .emboss-dot {
    width: 34px; height: 34px; border-radius: 50%;
    background: var(--emboss);
  }
  .emboss-name {
    color: var(--emboss); font-weight: 600; font-size: 34px; letter-spacing: 1px;
  }
</style>
</head>
<body>
<main class="canvas">
  <section class="card card-front">
    <div class="brand">
      <span class="brand-dot"></span>
      <span class="brand-name">Skylark Reelworks</span>
    </div>
    <p class="credentials">NRD Certified Remote Pilot<br>Fully Insured</p>
    <svg class="divider" width="520" height="297" aria-hidden="true">
      <line x1="270" y1="62" x2="252" y2="240" stroke="var(--orange)" stroke-width="1"/>
    </svg>
    <div class="person">
      <h1 class="person-name"><span class="first">Owen</span> <span class="last">Tarrick</span></h1>
      <p class="person-role">Owner</p>
      <ul class="contacts">
        <li>
          <svg viewBox="0 0 16 16" aria-hidden="true"><path fill="var(--orange)" d="M3.5 1.5l2.5 0 1 3.5-1.6 1.2a8 8 0 0 0 4.4 4.4L11 9l3.5 1v2.5c0 1-1 2-2 2A11 11 0 0 1 1.5 3.5c0-1 1-2 2-2z"/></svg>
          614-502-7738
        </li>
        <li>
          <svg viewBox="0 0 16 16" aria-hidden="true"><circle cx="8" cy="8" r="6.5" fill="none" stroke="var(--orange)" stroke-width="1.6"/><path d="M1.5 8h13M8 1.5c-3 3.5-3 9.5 0 13M8 1.5c3 3.5 3 9.5 0 13" fill="none" stroke="var(--orange)" stroke-width="1.2"/></svg>
          www.skylarkreelworks.example
        </li>
        <li>
          <svg viewBox="0 0 16 16" aria-hidden="true"><rect x="1" y="3" width="14" height="10" rx="1" fill="var(--orange)"/><path d="M1.5 3.8L8 9l6.5-5.2" fill="none" stroke="var(--navy)" stroke-width="1.3"/></svg>
          info@skylarkreelworks.example
        </li>
      </ul>
    </div>
  </section>
  <section class="card card-back">
    <div class="emboss-mark">
      <span class="emboss-dot"></span>
      <span class="emboss-name">Skylark Reelworks</span>
    </div>
  </section>
</main>
</body>
</html>
```